White Paper and One-Page Advertisement for TELVORISH-QM

I need both documents to be better formatted and designed so they look professional, not something someone with mediocre word skills put together. They will go out to 1000s of industry professionals, and they need to look sharp. I need them to have my company's color palate logo, and branding on it similar to how it is now, but better. Please do not change any of the written content, but it can be arranged in any other format you think is better. Smart art and things i've already used can be omitted in favor of better designs. The developer is free to use their creativity. White paper should not be longer than the three pages unless necessary.

Target Market(s)

Life Sciences supply chain professionals

Colors
33b8a4
0592cd
9bcb3c
fbee3e
3277b5

Requirements
Must have
• Must be professional looking and not look like something done in word. Please use the color palate as seen on the documents.
Should not have
• Any changes to the written content.

```html
<!DOCTYPE html>
<html lang="en">
<head>
<meta charset="utf-8">
<title>TELVORISH-QM White Paper</title>
<link href="https://fonts.googleapis.com/css2?family=Teko:wght@500;600&family=Roboto+Condensed:wght@400;700&family=Roboto:wght@400;700&display=swap" rel="stylesheet">
<style>
:root{
  --bg:#3d3d3d;
  --paper:#f7fbfc;
  --teal:#3aa9b9;
  --teal-dark:#2a8fa3;
  --teal-light:#7fcadb;
  --green:#86bc2e;
  --green-dark:#16977a;
  --gold:#cbc23a;
  --blue:#1d7fb8;
  --grey-dark:#555a5e;
  --grey:#8e9296;
  --text:#3b3f42;
  --white:#ffffff;
}
*{margin:0;padding:0;box-sizing:border-box}
html,body{width:1200px;height:900px;overflow:hidden;background:var(--bg)}
.spread{position:relative;width:1200px;height:900px}
.page{position:absolute;top:100px;width:496px;height:700px;background:var(--paper);overflow:hidden}
.cover{left:82px}
.overview{left:622px}
.page-art{position:absolute;inset:0}
/* cover */
.brand{position:absolute;left:30px;top:66px;display:flex;align-items:center;gap:8px;font:700 19px/1 "Roboto Condensed",sans-serif;color:var(--green-dark);letter-spacing:.5px}
.brand-dot{width:14px;height:14px;border-radius:50%;background:var(--green)}
.title{position:absolute;left:116px;top:232px;font-family:"Teko",sans-serif;font-weight:600;line-height:.9}
.title-line1{font-size:60px;color:var(--grey)}
.title-line2{font-size:78px;color:var(--grey-dark)}
.title-line3{font-size:44px;color:var(--teal);letter-spacing:.5px}
.subtitle{position:absolute;left:38px;top:420px;font:700 17.5px/1.3 "Roboto Condensed",sans-serif;color:var(--green)}
.author{position:absolute;right:30px;top:584px;text-align:center;color:var(--white);font-family:"Teko",sans-serif;font-weight:600}
.author-name{font-size:30px;line-height:1}
.author-date{font:700 15px/1.2 "Roboto Condensed",sans-serif}
/* overview */
.section-title{position:absolute;left:27px;top:26px;font:600 22px/1 "Teko",sans-serif;color:var(--blue);letter-spacing:.5px}
.intro{position:absolute;left:24px;top:47px;width:448px;padding:7px 10px;background:var(--teal);color:var(--white);font:400 8.3px/1.37 "Roboto",sans-serif;text-align:justify}
.stats{position:absolute;left:42px;top:170px;display:flex;gap:12px}
.stat{width:95px;height:58px;background:#e7eeee}
.stat-value{height:26px;font:600 17px/28px "Teko",sans-serif;color:var(--white);text-align:center;letter-spacing:.5px}
.stat-label{padding:5px 4px 0;font:700 5.4px/1.25 "Roboto Condensed",sans-serif;color:#555;text-align:center;text-transform:uppercase}
.stat-green .stat-value{background:var(--green)}
.stat-gold .stat-value{background:var(--gold)}
.stat-deep .stat-value{background:var(--green-dark)}
.stat-sky .stat-value{background:var(--teal-light)}
.question{position:absolute;left:48px;top:238px;font:400 11px/1 "Roboto Condensed",sans-serif;color:var(--blue)}
.meaning{position:absolute;left:84px;top:255px;width:340px;list-style:none;font:400 8.3px/1.3 "Roboto",sans-serif;color:var(--text)}
.meaning li{position:relative;padding-left:16px;margin-bottom:5px}
.meaning li::before{content:"";position:absolute;left:0;top:1px;width:9px;height:9px;border-radius:50%;border:2px solid var(--green);border-right-color:transparent}
.meaning li:nth-child(2)::before{border-color:var(--gold);border-right-color:transparent}
.meaning li:nth-child(3)::before{border-color:var(--green-dark);border-right-color:transparent}
.meaning li:nth-child(4)::before{border-color:var(--teal-light);border-right-color:transparent}
.example{display:block;margin:4px 0 0 36px;font-weight:700;color:var(--green)}
.body-col{position:absolute;top:386px;width:204px;font:400 7.9px/1.42 "Roboto",sans-serif;color:var(--text);text-align:justify}
.col-left{left:34px}
.col-right{left:259px}
.body-col p{margin-bottom:9px}
.sub-head{font:600 13px/1 "Teko",sans-serif;color:var(--blue);margin:14px 0 5px;letter-spacing:.3px}
.sub-q{font:400 10px/1 "Roboto Condensed",sans-serif;color:var(--teal);margin-bottom:4px}
.problems{list-style:none}
.problems li{position:relative;padding-left:10px;margin-bottom:3px;text-align:left}
.problems li::before{content:"";position:absolute;left:0;top:3px;width:5px;height:5px;border-radius:50%;background:var(--teal)}
</style>
</head>
<body>
<main class="spread">

  <section class="page cover">
    <svg class="page-art" viewBox="0 0 496 700" aria-hidden="true">
      <polygon points="0,0 306,0 0,290" fill="#cfdde1"/>
      <polygon points="0,0 200,0 0,190" fill="#c4d6db"/>
      <polygon points="496,396 496,700 188,700 188,587" fill="var(--teal-dark)"/>
      <polygon points="0,493 188,587 188,700 0,700" fill="var(--teal-light)"/>
      <polygon points="0,560 188,700 0,700" fill="#5fbacb"/>
      <polygon points="496,470 496,700 188,700" fill="#2f97ab"/>
    </svg>
    <div class="brand"><span class="brand-dot"></span>TELVORISH-QM</div>
    <h1 class="title">
      <div class="title-line1">CHANGING</div>
      <div class="title-line2">PHARMA’S</div>
      <div class="title-line3">PARADIGM OF WASTE</div>
    </h1>
    <p class="subtitle">How Pharma's Demand Volatility<br>Could Be Costing You Millions in<br>Material Write-downs &amp; Procurement</p>
    <div class="author">
      <div class="author-name">DALE MARVEN</div>
      <div class="author-date">August 2018</div>
    </div>
  </section>

  <section class="page overview">
    <svg class="page-art" viewBox="0 0 496 700" aria-hidden="true">
      <polygon points="0,0 496,0 496,120 0,260" fill="#eef5f1"/>
      <polygon points="496,390 496,700 0,700 0,520 188,700" fill="#c3e3ea"/>
      <polygon points="0,510 188,700 0,700" fill="#a9d8e2"/>
      <polygon points="496,390 188,700 496,700" fill="#b2dde6"/>
    </svg>
    <h2 class="section-title">OVERVIEW</h2>
    <p class="intro">Demand volatility is a challenge for very supply chain. It strikes at the end of supply chains causing a "bullwhip effect" that becomes exponentially more impactful further back in the chain. For Pharma, the effect is strongest in manufacturing and procurement, specifically with starting raw materials and consumables. Swings in demand can cripple launches, cause stock-outs, inflate material prices, make lean planning ineffective, and cause significant write-downs of residual/obsolete materials; ultimately inflating CoGS and reducing net income. These swings can also cause inventory costs to inflate, materials to expire or become obsolete, higher disposal fees, and a larger carbon footprint. The yearly financial impacts are staggering considering Pharma's economic footprint. Twenty of Pharma's top 100 companies were sampled using 2015 &amp; 2016 financial figures1-2-3-4. Industry estimates for waste include:</p>

    <div class="stats">
      <div class="stat stat-green"><div class="stat-value">3.77%</div><div class="stat-label">Avg raw material write-down as a % of net income</div></div>
      <div class="stat stat-gold"><div class="stat-value">$ 2.7 B</div><div class="stat-label">Est pharma written down inventory in 2016</div></div>
      <div class="stat stat-deep"><div class="stat-value">$ 2,034</div><div class="stat-label">Est US pharma revenue per 1 ton non-MSW waste</div></div>
      <div class="stat stat-sky"><div class="stat-value">.01</div><div class="stat-label">Correlation coefficient of material write-downs and firm size</div></div>
    </div>

    <h3 class="question">What do these numbers mean?</h3>
    <ul class="meaning">
      <li>3.77% is an alarmingly high, and does not include capitalized consumables, equipment disposal, and similar wastes
        <span class="example">$5B in net income LS Firm: est $185M in write-downs<br>$50M in net income LS Firm: est $1.9M in write-downs</span></li>
      <li>$2.7B is likely much lower than the real figure due to capitalizing consumable inventories for launches etc.</li>
      <li>$2,034 to one ton of industrial waste is not progressive.</li>
      <li>.01 correlation coefficient means this problem does not discriminate based on company size and is ubiquitous in the industry.</li>
    </ul>

    <div class="body-col col-left">
      <p>Industries have attempted to mitigate the bullwhip effect through many techniques and systems such as ERP, robust forecasting models, demand management, LSS tools, strategic sourcing, etc. However, life science firms still struggle to effectively address this problem as evidenced by the write-down figures. Many non-FDA regulated industries have started utilizing marketplaces and brokerage services to create circular supply chains that optimize waste by connecting buyers and sellers. However, Pharma and life sciences have yet to adopt this waste-centric supply chain and execute it in a manner conducive to the compliance and indemnification requirements of the industry regarding primary and secondary transactions of raw materials, equipment, consumables, spare parts, and collaborative relationships. Finished products such as APIs, intermediates, and devices are out of scope for this supply chain.</p>
      <p><strong>A life sciences marketplace and consortium</strong> for manufacturuers, reseraechers, and vendors canminimize the aforementioned problems by quickly, innovatively, and transparently exchanging material information in safe and controlled environment ensuring a firm's standards for data</p>
    </div>
    <div class="body-col col-right">
      <p>integrity, cGMP compliance, contractual indemnification, and financial benefits are met; all by leveraging core auditing skills.</p>
      <p>It is a call to arms among supply chain, procurement, and quality leaders to take part in a more circular, greener, and collaborative supply chain.Time is critical as global competition grows, customer and government emphasis on lowering pricing mounts<sup>5</sup>, and collective pressure on sustainability demands widespread action.</p>
      <p>Let's explore Current and Future State of this industry issue to understand why such a marketplace can begin the much-needed transition for life science companies.</p>
      <h4 class="sub-head">BASELINE PROBLEM</h4>
      <div class="sub-q">What?</div>
      <ul class="problems">
        <li>Disposal of high quality materials, equipment, spare parts</li>
        <li>Single and/or limited sources of supply</li>
        <li>Inability to collaborative with like-minded life sciences firms</li>
      </ul>
    </div>
  </section>

</main>
</body>
</html>
```